RIVERSTONE PULSE GYM FLYER DESIGN

We want a flyer designed for our gym. We have an example of a flyer which we like and I have put it into the images I have uploaded. I would like to recreate using our pictures, so its a pretty straight forward job. We also want to put our weekly timetable on the back of the flyer. We would like the size of the flyer to be A5.

Target Market(s)

FITNESS

Industry/Entity Type

Gym

Colors
33a6d7
ffffff

Requirements
Must have
• We just want to recreate the flyer but we must have the following info on the flyer and we want our timetable on the back of the flyer which you can get from this link: http://www.riverstonepulsegym-example.com/timetable
• Riverstone Pulse Gym is a fun community of humble people. Our goal is to help guide you towards a fitter, healthier lifestyle!
• Our Programs
• HIIT
• High intensity interval training is 30-45 minutes of fat burning fun. The class is a mix of cardio, bodyweight and some resistance movements.
• Conditioning
• A full hour of strength, cardio and bodyweight training to get you in tip top shape. Expect a mix of barbells, kettlebells, rowing machines, bikes and other training methods.
• BWS
• This is our big Friday session to set you up for the weekend. 90 minutes of hard training that is done with a team emphasis. From heavy lifting to cardio triathlons, this class has it all but not for the faint hearted.
• Muay Thai
• Commonly known as the science of 8 limbs you will learn how to punch, kick, knee and elbow. Thailands national sport is a great way to get your fitness kick. We train the complete beginner all the way to international fighters so you are in great hands.
• Kids Muay Thai
• Our junior program starts from age 6 onwards. Muay Thai is a great way for kids to get active and fit while learning new skills. Training in martial arts also teaches self discipline and socialisation skills.
• Yoga
• A combination of physical and mental practises that will leave you focused and refreshed for whatever the week throws at you. We always recommend our yoga classes as a great way to balance the high intensity training we offer.
• Q-Press
• Strength training with a little bit of conditioning. We regularly update the program and re test lifts to ensure you are making progress and getting stronger.
• CONTACT US
• OUR LOCATION:
• Unit 27C
• 214 Kelvane Road
• Marrow Heath
• Glasgow
• G72QT
• Phone: 07930625184
• Email: info@riverstonepulsegym-example.com
• Web: www.riverstonepulsegym-example.com
Nice to have
• Can use all the picture but if not be good to use the boxing one and the group training one.

```html
<!DOCTYPE html>
<html lang="en">
<head>
<meta charset="utf-8">
<title>Riverstone Pulse Gym – A5 Flyer</title>
<link href="https://fonts.googleapis.com/css2?family=Oswald:wght@400;500;700&family=Open+Sans:wght@400;600;700&display=swap" rel="stylesheet">
<style>
:root{
  --brand:#33a6d7;
  --brand-deep:#1f86b8;
  --navy:#163a55;
  --ink:#1a232c;
  --white:#ffffff;
  --paper:#eceff2;
  --row:#f4f8fb;
  --row-alt:#e2eef5;
}
*{box-sizing:border-box;margin:0;padding:0}
html,body{width:867px;height:1200px;overflow:hidden;background:var(--paper)}
body{font-family:"Open Sans",Arial,sans-serif;color:var(--white);position:relative}
.sheet{position:absolute;left:24px;width:819px;height:560px;background:var(--brand);overflow:hidden;box-shadow:0 3px 10px rgba(0,0,0,.18)}
.sheet--front{top:28px}
.sheet--back{top:612px}
.photo{position:absolute}
.heading{font-family:"Oswald",Arial,sans-serif;font-weight:700;text-transform:uppercase;letter-spacing:.5px}

/* front */
.intro{position:absolute;left:0;top:0;width:240px;height:250px;background:var(--navy);padding:18px 20px}
.intro__title{font-size:25px;line-height:1.1;color:var(--white)}
.intro__text{font-size:10px;line-height:1.5;margin-top:10px}
.join{margin-top:14px;display:inline-block;background:var(--brand);font-family:"Oswald",Arial,sans-serif;font-size:13px;font-weight:500;padding:3px 14px;text-transform:uppercase}
.intro__web{display:block;font-size:9px;margin-top:8px;white-space:nowrap}
.photo--group{left:240px;top:0;width:579px;height:168px;background:linear-gradient(135deg,#5b6670,#2d3339 60%,#4a3b36)}
.photo--kettlebell{left:0;top:250px;width:240px;height:270px;background:linear-gradient(160deg,#8a8f94,#4a4d52 55%,#7c3a2e)}
.programs{position:absolute;left:240px;top:168px;width:300px;height:352px;padding:14px 18px 0 18px}
.programs__title{font-size:26px;margin-bottom:10px}
.program{display:flex;gap:10px;margin-bottom:10px}
.program__icon{flex:0 0 18px;height:18px;margin-top:1px}
.program__name{font-family:"Oswald",Arial,sans-serif;font-size:13px;font-weight:500;text-transform:uppercase;line-height:1.1}
.program__desc{font-size:9px;line-height:1.38;margin-top:2px}
.programs--side{left:540px;width:279px;background:var(--brand-deep);padding-top:18px}
.programs--side .program{margin-bottom:14px}
.contact{position:absolute;left:0;bottom:0;width:819px;height:40px;background:var(--navy);display:flex;align-items:center;gap:36px;padding:0 20px;font-size:10px}
.contact__label{font-family:"Oswald",Arial,sans-serif;font-size:15px;font-weight:500;text-transform:uppercase}
.contact__item{display:flex;align-items:center;gap:6px}

/* back */
.timetable{position:absolute;left:0;top:0;width:540px;height:520px;padding:16px 14px;display:grid;grid-template-columns:repeat(3,1fr);grid-template-rows:1fr 1fr;gap:14px 10px}
.day{background:var(--white);color:var(--ink);display:flex;flex-direction:column}
.day__name{background:var(--navy);color:var(--white);font-family:"Oswald",Arial,sans-serif;font-size:13px;font-weight:500;text-transform:uppercase;padding:4px 8px}
.day__row{display:flex;gap:8px;font-size:9.5px;padding:0 8px;flex:1;align-items:center;border-bottom:1px solid #cfe0ea}
.day__row:nth-child(odd){background:var(--row-alt)}
.day__row:nth-child(even){background:var(--row)}
.day__time{width:32px;font-weight:700;color:var(--brand-deep)}
.photo--boxer{left:540px;top:0;width:279px;height:300px;background:linear-gradient(170deg,#3a4047,#1f2428 55%,#5a4a42)}
.brand-panel{position:absolute;left:540px;top:300px;width:279px;height:220px;background:var(--brand-deep);text-align:center;padding:40px 12px 0}
.brand-panel__mark{display:inline-flex;align-items:center;gap:8px;white-space:nowrap}
.brand-panel__square{width:14px;height:14px;background:var(--white);flex:0 0 14px}
.brand-panel__name{font-family:"Oswald",Arial,sans-serif;font-weight:700;font-size:19px;text-transform:uppercase;letter-spacing:.5px}
.brand-panel__address{font-size:10px;line-height:1.5;margin-top:18px}
.brand-panel__web{font-size:10px;font-weight:700;margin-top:8px}
</style>
</head>
<body>

<section class="sheet sheet--front">
  <div class="intro">
    <h1 class="heading intro__title">No experience?<br>No problem!</h1>
    <p class="intro__text">Riverstone Pulse Gym is a fun community of humble people. Our goal is to help guide you towards a fitter, healthier lifestyle!</p>
    <span class="join">Join today!</span>
    <span class="intro__web">www.riverstonepulsegym-example.com</span>
  </div>
  <div class="photo photo--group" role="img" aria-label="Photo of a group training class in the gym"></div>
  <div class="photo photo--kettlebell" role="img" aria-label="Photo of a woman training with a kettlebell"></div>

  <div class="programs">
    <h2 class="heading programs__title">Our programs</h2>
    <div class="program">
      <svg class="program__icon" viewBox="0 0 18 18"><circle cx="9" cy="9" r="9" fill="#fff"/><path d="M5 9.3l2.6 2.6L13 6.5" stroke="#33a6d7" stroke-width="2" fill="none"/></svg>
      <div><h3 class="program__name">HIIT</h3><p class="program__desc">High intensity interval training is 30-45 minutes of fat burning fun. The class is a mix of cardio, bodyweight and some resistance movements.</p></div>
    </div>
    <div class="program">
      <svg class="program__icon" viewBox="0 0 18 18"><circle cx="9" cy="9" r="9" fill="#fff"/><path d="M5 9.3l2.6 2.6L13 6.5" stroke="#33a6d7" stroke-width="2" fill="none"/></svg>
      <div><h3 class="program__name">Conditioning</h3><p class="program__desc">A full hour of strength, cardio and bodyweight training to get you in tip top shape. Expect a mix of barbells, kettlebells, rowing machines, bikes and other training methods.</p></div>
    </div>
    <div class="program">
      <svg class="program__icon" viewBox="0 0 18 18"><circle cx="9" cy="9" r="9" fill="#fff"/><path d="M5 9.3l2.6 2.6L13 6.5" stroke="#33a6d7" stroke-width="2" fill="none"/></svg>
      <div><h3 class="program__name">BWS</h3><p class="program__desc">This is our big Friday session to set you up for the weekend. 90 minutes of hard training that is done with a team emphasis. From heavy lifting to cardio triathlons, this class has it all but not for the faint hearted.</p></div>
    </div>
    <div class="program">
      <svg class="program__icon" viewBox="0 0 18 18"><circle cx="9" cy="9" r="9" fill="#fff"/><path d="M5 9.3l2.6 2.6L13 6.5" stroke="#33a6d7" stroke-width="2" fill="none"/></svg>
      <div><h3 class="program__name">Q-Press</h3><p class="program__desc">Strength training with a little bit of conditioning. We regularly update the program and re test lifts to ensure you are making progress and getting stronger.</p></div>
    </div>
  </div>

  <div class="programs programs--side">
    <div class="program">
      <svg class="program__icon" viewBox="0 0 18 18"><circle cx="9" cy="9" r="9" fill="#fff"/><path d="M5 9.3l2.6 2.6L13 6.5" stroke="#1f86b8" stroke-width="2" fill="none"/></svg>
      <div><h3 class="program__name">Muay Thai</h3><p class="program__desc">Commonly known as the science of 8 limbs you will learn how to punch, kick, knee and elbow. Thailands national sport is a great way to get your fitness kick. We train the complete beginner all the way to international fighters so you are in great hands.</p></div>
    </div>
    <div class="program">
      <svg class="program__icon" viewBox="0 0 18 18"><circle cx="9" cy="9" r="9" fill="#fff"/><path d="M5 9.3l2.6 2.6L13 6.5" stroke="#1f86b8" stroke-width="2" fill="none"/></svg>
      <div><h3 class="program__name">Kids Muay Thai</h3><p class="program__desc">Our junior program starts from age 6 onwards. Muay Thai is a great way for kids to get active and fit while learning new skills. Training in martial arts also teaches self discipline and socialisation skills.</p></div>
    </div>
    <div class="program">
      <svg class="program__icon" viewBox="0 0 18 18"><circle cx="9" cy="9" r="9" fill="#fff"/><path d="M5 9.3l2.6 2.6L13 6.5" stroke="#1f86b8" stroke-width="2" fill="none"/></svg>
      <div><h3 class="program__name">Yoga</h3><p class="program__desc">A combination of physical and mental practises that will leave you focused and refreshed for whatever the week throws at you. We always recommend our yoga classes as a great way to balance the high intensity training we offer.</p></div>
    </div>
  </div>

  <footer class="contact">
    <span class="contact__label">Contact us</span>
    <span class="contact__item"><svg width="12" height="12" viewBox="0 0 12 12"><path d="M2.5 1h2l1 3-1.5 1a7 7 0 0 0 3 3l1-1.5 3 1v2a1 1 0 0 1-1 1A10 10 0 0 1 1.5 2a1 1 0 0 1 1-1z" fill="#fff"/></svg>07700 900184</span>
    <span class="contact__item"><svg width="13" height="10" viewBox="0 0 13 10"><rect x=".5" y=".5" width="12" height="9" fill="none" stroke="#fff"/><path d="M.5.5l6 5 6-5" fill="none" stroke="#fff"/></svg>info@riverstonepulsegym-example.com</span>
    <span class="contact__item">www.riverstonepulsegym-example.com</span>
  </footer>
</section>

<section class="sheet sheet--back">
  <div class="timetable">
    <div class="day"><div class="day__name">Monday</div>
      <div class="day__row"><span class="day__time">06:30</span>HIIT</div>
      <div class="day__row"><span class="day__time">09:00</span>Open Gym</div>
      <div class="day__row"><span class="day__time">12:15</span>HIIT</div>
      <div class="day__row"><span class="day__time">17:00</span>Kids Muay Thai</div>
      <div class="day__row"><span class="day__time">18:00</span>Conditioning</div>
      <div class="day__row"><span class="day__time">19:00</span>Muay Thai</div>
      <div class="day__row"><span class="day__time">20:00</span>Yoga</div>
    </div>
    <div class="day"><div class="day__name">Tuesday</div>
      <div class="day__row"><span class="day__time">06:30</span>Conditioning</div>
      <div class="day__row"><span class="day__time">09:00</span>Open Gym</div>
      <div class="day__row"><span class="day__time">12:15</span>Q-Press</div>
      <div class="day__row"><span class="day__time">17:30</span>HIIT</div>
      <div class="day__row"><span class="day__time">18:30</span>Muay Thai</div>
      <div class="day__row"><span class="day__time">19:30</span>Q-Press</div>
      <div class="day__row"><span class="day__time">20:30</span>Open Gym</div>
    </div>
    <div class="day"><div class="day__name">Wednesday</div>
      <div class="day__row"><span class="day__time">06:30</span>HIIT</div>
      <div class="day__row"><span class="day__time">09:00</span>Yoga</div>
      <div class="day__row"><span class="day__time">12:15</span>Conditioning</div>
      <div class="day__row"><span class="day__time">17:00</span>Kids Muay Thai</div>
      <div class="day__row"><span class="day__time">18:00</span>HIIT</div>
      <div class="day__row"><span class="day__time">19:00</span>Muay Thai</div>
      <div class="day__row"><span class="day__time">20:00</span>Q-Press</div>
    </div>
    <div class="day"><div class="day__name">Thursday</div>
      <div class="day__row"><span class="day__time">06:30</span>Q-Press</div>
      <div class="day__row"><span class="day__time">09:00</span>Open Gym</div>
      <div class="day__row"><span class="day__time">12:15</span>HIIT</div>
      <div class="day__row"><span class="day__time">17:30</span>Conditioning</div>
      <div class="day__row"><span class="day__time">18:30</span>Muay Thai</div>
      <div class="day__row"><span class="day__time">19:30</span>Yoga</div>
      <div class="day__row"><span class="day__time">20:30</span>Open Gym</div>
    </div>
    <div class="day"><div class="day__name">Friday</div>
      <div class="day__row"><span class="day__time">06:30</span>HIIT</div>
      <div class="day__row"><span class="day__time">09:00</span>Open Gym</div>
      <div class="day__row"><span class="day__time">12:15</span>Conditioning</div>
      <div class="day__row"><span class="day__time">17:00</span>Kids Muay Thai</div>
      <div class="day__row"><span class="day__time">18:00</span>BWS</div>
      <div class="day__row"><span class="day__time">19:30</span>Muay Thai</div>
      <div class="day__row"><span class="day__time">20:30</span>Open Gym</div>
    </div>
    <div class="day"><div class="day__name">Saturday</div>
      <div class="day__row"><span class="day__time">09:00</span>BWS</div>
      <div class="day__row"><span class="day__time">10:30</span>Yoga</div>
      <div class="day__row"><span class="day__time">11:30</span>Open Gym</div>
      <div class="day__row"><span class="day__time">12:30</span>Muay Thai</div>
      <div class="day__row"><span class="day__time">13:30</span>Kids Muay Thai</div>
      <div class="day__row"><span class="day__time">14:30</span>Open Gym</div>
      <div class="day__row"><span class="day__time">15:30</span>Q-Press</div>
    </div>
  </div>

  <div class="photo photo--boxer" role="img" aria-label="Photo of a boxer training in the gym"></div>

  <div class="brand-panel">
    <div class="brand-panel__mark"><span class="brand-panel__square"></span><span class="brand-panel__name">Riverstone Pulse Gym</span></div>
    <p class="brand-panel__address">Unit 27C, 214 Kelvane Road<br>Marrow Heath, Glasgow<br>G72QT</p>
    <p class="brand-panel__web">www.riverstonepulsegym-example.com</p>
  </div>

  <footer class="contact">
    <span class="contact__label">Contact us</span>
    <span class="contact__item"><svg width="12" height="12" viewBox="0 0 12 12"><path d="M2.5 1h2l1 3-1.5 1a7 7 0 0 0 3 3l1-1.5 3 1v2a1 1 0 0 1-1 1A10 10 0 0 1 1.5 2a1 1 0 0 1 1-1z" fill="#fff"/></svg>07700 900184</span>
    <span class="contact__item"><svg width="13" height="10" viewBox="0 0 13 10"><rect x=".5" y=".5" width="12" height="9" fill="none" stroke="#fff"/><path d="M.5.5l6 5 6-5" fill="none" stroke="#fff"/></svg>info@riverstonepulsegym-example.com</span>
    <span class="contact__item">www.riverstonepulsegym-example.com</span>
  </footer>
</section>

</body>
</html>
```